RW Framewell Inc Business cards

We need business cards using our existing logo but slightly modified. Right now the logo says RW Loadbearing Masonry. We want to keep the RW part of the design, but replace the Structural Concrete portion with "FRAMEWELL". Please see the attached file.
Ideally this would be a blank template so we can add Different Names, titles, and phone numbers later.
On the one side we want only the logo and on the other side the detail. I'm attaching an example for you to see.
Please reach out with any other questions. Our address and other details will be given out once we find a design we like.

Target Market(s)

Construction Industry

```html
<!DOCTYPE html>
<html lang="en">
<head>
<meta charset="utf-8">
<title>RW Framewell Inc — Business Cards</title>
<link href="https://fonts.googleapis.com/css2?family=Montserrat:wght@400;500;600;700&display=swap" rel="stylesheet">
<style>
  :root {
    --canvas: #dedee0;
    --brand-blue: #1a5f94;
    --bright-blue: #1f74bc;
    --slate: #7b7c80;
    --ink: #2b2b2b;
    --white: #ffffff;
  }
  * { margin: 0; padding: 0; box-sizing: border-box; }
  html, body { width: 1200px; height: 1200px; overflow: hidden; }
  body {
    background: var(--canvas);
    font-family: "Montserrat", sans-serif;
    position: relative;
  }
  .card {
    position: absolute;
    left: 182px;
    width: 833px;
    height: 472px;
    overflow: hidden;
  }
  .card--front { top: 101px; background: var(--brand-blue); }
  .card--back  { top: 616px; background: var(--white); }

  .wordmark {
    position: absolute;
    display: flex;
    flex-direction: column;
    align-items: center;
    font-weight: 600;
    line-height: 1;
  }
  .wordmark__initials { font-size: 132px; letter-spacing: 6px; }
  .wordmark__name { font-size: 42px; letter-spacing: 10px; margin-top: 14px; }
  .card--front .wordmark {
    color: var(--white);
    left: 0; right: 0; top: 140px;
  }
  .card--back .wordmark {
    color: var(--bright-blue);
    left: 88px; width: 232px; top: 142px;
  }
  .card--back .wordmark__initials { font-size: 82px; letter-spacing: 4px; }
  .card--back .wordmark__name { font-size: 26px; letter-spacing: 5px; margin-top: 10px; }

  .person {
    position: absolute;
    left: 435px; top: 67px;
    font-size: 29px; font-weight: 700;
    color: var(--slate);
    letter-spacing: 0.3px;
  }
  .person__surname { color: var(--brand-blue); }
  .role {
    position: absolute;
    left: 436px; top: 109px;
    font-size: 16px; font-weight: 500;
    color: var(--ink);
  }
  .role-rule {
    position: absolute;
    left: 635px; top: 119px;
    width: 198px; height: 2px;
    background: var(--brand-blue);
  }
  .contact {
    position: absolute;
    left: 437px;
    display: flex;
    align-items: center;
    gap: 14px;
    font-size: 17px;
    color: var(--ink);
    line-height: 1.35;
  }
  .contact--phone { top: 164px; }
  .contact--email { top: 228px; }
  .contact--address { top: 292px; }
  .contact__icon { width: 48px; height: 48px; flex: none; }
  .footer-bands { position: absolute; left: 0; bottom: 0; }
</style>
</head>
<body>

<section class="card card--front" aria-label="Business card front">
  <div class="wordmark">
    <span class="wordmark__initials">RW</span>
    <span class="wordmark__name">FRAMEWELL</span>
  </div>
</section>

<section class="card card--back" aria-label="Business card back">
  <div class="wordmark">
    <span class="wordmark__initials">RW</span>
    <span class="wordmark__name">FRAMEWELL</span>
  </div>

  <h1 class="person">DANIEL <span class="person__surname">BROOKS</span></h1>
  <p class="role">Chief Executive Officer</p>
  <div class="role-rule"></div>

  <div class="contact contact--phone">
    <svg class="contact__icon" viewBox="0 0 48 48" aria-hidden="true">
      <rect width="48" height="48" fill="var(--bright-blue)"/>
      <polygon points="48,0 48,48 0,48" fill="var(--brand-blue)"/>
      <rect x="17" y="10" width="14" height="28" rx="2" fill="var(--white)"/>
      <rect x="19" y="13" width="10" height="19" fill="var(--brand-blue)"/>
      <circle cx="24" cy="35" r="1.3" fill="var(--brand-blue)"/>
    </svg>
    <span>555 . 204 &nbsp;31786620</span>
  </div>

  <div class="contact contact--email">
    <svg class="contact__icon" viewBox="0 0 48 48" aria-hidden="true">
      <rect width="48" height="48" fill="var(--bright-blue)"/>
      <polygon points="48,0 48,48 0,48" fill="var(--brand-blue)"/>
      <rect x="10" y="15" width="28" height="19" fill="none" stroke="var(--white)" stroke-width="2"/>
      <polyline points="10,15 24,27 38,15" fill="none" stroke="var(--white)" stroke-width="2"/>
      <line x1="10" y1="34" x2="20" y2="24" stroke="var(--white)" stroke-width="2"/>
      <line x1="38" y1="34" x2="28" y2="24" stroke="var(--white)" stroke-width="2"/>
    </svg>
    <span>hello@danielbrooks.net</span>
  </div>

  <div class="contact contact--address">
    <svg class="contact__icon" viewBox="0 0 48 48" aria-hidden="true">
      <rect width="48" height="48" fill="var(--bright-blue)"/>
      <polygon points="48,0 48,48 0,48" fill="var(--brand-blue)"/>
      <path d="M24 39 C24 39 13 27 13 20 A11 11 0 0 1 35 20 C35 27 24 39 24 39 Z" fill="var(--white)"/>
      <circle cx="24" cy="20" r="4.5" fill="var(--bright-blue)"/>
    </svg>
    <span>Address here, Suite#1<br>New Avenue, NY -012</span>
  </div>

  <svg class="footer-bands" width="833" height="54" viewBox="0 0 833 54" aria-hidden="true">
    <polygon points="0,0 392,0 422,54 0,54" fill="var(--slate)"/>
    <polygon points="408,0 833,0 833,54 438,54" fill="var(--brand-blue)"/>
  </svg>
</section>

</body>
</html>
```